TREVAL BUILDWORKS, LLC Webpage portfolio

I want to create a Website that allows my potential clients to browse my Skilled work via before and after photos. I want the website to enhance the work that I provide and potentially drive new business, or at least solidify my work.
I also do 3D CAD and Modeling of New Spaces and it would be nice to show some of that work from pencil design to 3D modeling, which I feel may help give me more clients.

The website needs to show a solid carpenter/company with the skills to get any project completed.

Types of Jobs - Custom Carpentry & Finishes, Kitchens, Baths, Basements, Decks, Porches, Whole House Renovation - Skilled Craftsmanship (Hardwood Flooring, Floor and Wall Tile) and much more...

Target Market(s)

Residential Home Renovation, Kitchen and Bath Renovation, Home Improvement

Industry/Entity Type

Residential Construction

Number of Pages Required

5+ page

Font styles to use
Sans Serif
Script

Requirements
Must have
• Similar to Plinvo.com, except for Treval Buildworks.
• Must be inviting.
• My Services Offered
• A way to reach me or contact me for estimates with some sort of Screening Questionare.
Nice to have
• Inviting Colors
Should not have
• Not sure at this time

```html
<!DOCTYPE html>
<html lang="en">
<head>
<meta charset="utf-8">
<title>Treval Buildworks — Portfolio</title>
<link href="https://fonts.googleapis.com/css2?family=Poiret+One&family=Quicksand:wght@500;600;700&display=swap" rel="stylesheet">
<style>
:root{
  --bg:#262626;
  --stripe:#1b1b1b;
  --ink:#f2f2f2;
  --muted:#d2d2d2;
  --panel-dark:#161616;
}
*{margin:0;padding:0;box-sizing:border-box}
html,body{width:758px;height:1200px;overflow:hidden}
body{
  position:relative;
  background:var(--bg) repeating-linear-gradient(90deg,var(--stripe) 0 2px,transparent 2px 6px);
  color:var(--ink);
  font-family:"Quicksand",sans-serif;
}
.abs{position:absolute}
.brand{left:32px;top:29px;display:flex;align-items:center;gap:6px;font:700 11px "Quicksand",sans-serif;color:#c8c8c8}
.brand-mark{width:12px;height:12px;border-radius:50%;background:#c8c8c8}
.phone{right:32px;top:12px;font-size:7px;font-weight:500}
.social{display:flex;gap:9px;align-items:center}
.social span{width:8px;height:8px;border-radius:2px;border:1.5px solid var(--ink)}
.top-social{left:561px;top:13px}
.nav{right:32px;top:49px;display:flex;gap:13px;font-size:9px;font-weight:500;letter-spacing:.2px}
.heading{left:31px;font:400 21px/27px "Poiret One",sans-serif;letter-spacing:1px;text-transform:uppercase;z-index:2}
.small{left:31px;font-size:6.5px;line-height:9px;font-weight:600;text-transform:uppercase;z-index:2}
.panel{left:86px;width:640px}
.services{top:95px;height:315px;display:flex;overflow:hidden}
.seg{flex:1;height:100%}
.seg-draw{background:linear-gradient(180deg,#868686,#7a7a7a 60%,#747474)}
.seg-mid{background:
  radial-gradient(ellipse 40% 30% at 60% 45%,rgba(200,200,200,.35),transparent 70%),
  linear-gradient(180deg,#6e6e6e,#5c5c5c 55%,#4e4e4e 85%,#5a5a5a)}
.seg-photo{background:
  linear-gradient(180deg,transparent 72%,rgba(60,35,20,.55) 72%,rgba(120,75,40,.9) 100%),
  radial-gradient(ellipse 30% 30% at 40% 42%,#c9c4b4,#9b8f76 60%,transparent 75%),
  linear-gradient(90deg,#7a4b2e,#9c6a44 25%,#a8865f 55%,#b98b5d 80%,#6e4a30)}
.browse{top:474px;height:315px;background:
  radial-gradient(ellipse 38% 22% at 46% 20%,rgba(150,135,95,.9),rgba(95,80,55,.6) 60%,transparent 75%),
  radial-gradient(ellipse 30% 35% at 48% 45%,#3a2d20,transparent 70%),
  linear-gradient(90deg,#5a3a22,#3a2818 25%,#241a12 55%,#1e1510 80%,#3a2416)}
.thumb{left:118px;top:662px;width:190px;height:95px;background:
  linear-gradient(165deg,transparent 55%,rgba(90,65,40,.9) 55%),
  linear-gradient(90deg,#6b4a30,#8a5e3a 30%,#b08850 60%,#d8c7a0)}
.label{font-size:9px;font-weight:500;letter-spacing:.3px}
.testimonials{top:853px;height:283px;background:
  radial-gradient(ellipse at 70% 40%,#1d1d1d,transparent 70%),var(--panel-dark)}
.quote{top:946px;width:100px;text-align:right;font-size:6.5px;line-height:9px;color:var(--muted)}
.quote .name{margin-top:12px;font-size:9px;color:var(--ink);letter-spacing:.4px}
.quote .role{font-size:6.5px;color:var(--ink)}
.quote .stars{margin-top:8px;letter-spacing:2px;font-size:7px;color:#bdbdbd}
.estimate{right:72px;top:1094px;font:400 15px "Poiret One",sans-serif;letter-spacing:1px}
</style>
</head>
<body>
<div class="abs brand"><span class="brand-mark"></span>Treval Buildworks</div>
<div class="abs social top-social"><span></span><span></span><span></span><span></span></div>
<div class="abs phone">+8 (555) 014-22-90</div>
<nav class="abs nav"><span>KITCHENS</span><span>BATHS</span><span>BASEMENTS</span><span>FINISHED CARPENTRY</span><span>DECKS &amp; PORCHES</span></nav>

<div class="abs panel services">
  <div class="seg seg-draw" role="img" aria-label="Line drawing of a kitchen design"></div>
  <div class="seg seg-mid" role="img" aria-label="3D model of the kitchen"></div>
  <div class="seg seg-photo" role="img" aria-label="Photo of the finished kitchen"></div>
</div>
<h2 class="abs heading" style="top:93px">My<br>Services</h2>
<div class="abs small" style="top:189px">3D CAD modelling of new<br>spaces<br><br>custom<br>carpentry &amp; finishes,<br><br>kitchens,<br>baths,<br>basements,<br>decks,<br>porches,</div>
<div class="abs small" style="top:299px"><span style="font-size:10px;line-height:14px;font-weight:500">Whole house<br>renovation</span><br>skilled craftsmanship<br>(hardwood flooring,<br>floor and wall tile)<br><br>and much more</div>

<div class="abs panel browse" role="img" aria-label="Photo of a granite kitchen table with chairs"></div>
<h2 class="abs heading" style="top:471px">Browse<br>my work</h2>
<div class="abs small" style="top:567px;left:33px">Brose my work in<br>before and after<br>photos</div>
<svg class="abs" style="left:31px;top:631px" width="50" height="14" viewBox="0 0 50 14"><path d="M11 1L1 7l10 6z" fill="#fff"/><path d="M35 1l10 6-10 6z" fill="#fff"/></svg>
<div class="abs thumb" role="img" aria-label="Before photo of a stone porch"></div>
<div class="abs label" style="left:129px;top:741px">BEFORE</div>
<div class="abs label" style="left:129px;top:764px">AFTER</div>
<div class="abs social" style="left:31px;top:767px;gap:8px"><span style="width:7px;height:7px;border-width:1.2px"></span><span style="width:7px;height:7px;border-width:1.2px"></span><span style="width:7px;height:7px;border-width:1.2px"></span><span style="width:7px;height:7px;border-width:1.2px"></span></div>

<div class="abs panel testimonials"></div>
<h2 class="abs heading" style="top:851px">Clients<br>Testimonials</h2>
<div class="abs small" style="top:946px">Read what our happy<br>clients have to say<br>about our expertise and<br>services</div>

<div class="abs quote" style="left:272px">Lorem ipsum<br>dolor sit amet, con-<br>sectetur adipiscing elit.<br>Fusce sit amet ultri-<br>cies magna. ..<div class="name">JOHN DOE</div><div class="role">Entrepreneur</div><div class="stars">★★★★★</div></div>
<div class="abs quote" style="left:379px">Lorem ipsum<br>dolor sit amet, con-<br>sectetur adipiscing elit.<br>Fusce sit amet ultri-<br>cies magna. ..<div class="name">JOHN DOE</div><div class="role">Entrepreneur</div><div class="stars">★★★★★</div></div>
<div class="abs quote" style="left:487px">Lorem ipsum<br>dolor sit amet, con-<br>sectetur adipiscing elit.<br>Fusce sit amet ultri-<br>cies magna. ..<div class="name">JOHN DOE</div><div class="role">Entrepreneur</div><div class="stars">★★★★★</div></div>
<div class="abs quote" style="left:594px">Lorem ipsum<br>dolor sit amet, con-<br>sectetur adipiscing elit.<br>Fusce sit amet ultri-<br>cies magna. ..<div class="name">JOHN DOE</div><div class="role">Entrepreneur</div><div class="stars">★★★★★</div></div>

<div class="abs social" style="left:31px;top:1099px;gap:11px"><span style="width:10px;height:10px"></span><span style="width:10px;height:10px"></span><span style="width:10px;height:10px"></span><span style="width:10px;height:10px"></span></div>
<div class="abs estimate">REQUEST AN ESTIMATE</div>
</body>
</html>
```